Basic / Quick Business Card

Quick easy design project!

Need a one sided basic business card that matches font & style of brand and bottle label for our gourmet condiment, Brindle Harrow Sauce. Brindle Harrow Sauce is sold in specialty retail, gourmet groceries and appears on chef-driven restaurant menus, so the target market is a high end, gourmet, artisan-made food-loving customer.

Files Included:
Sauce Bottle Label
Brindle Harrow Sauce Round Logos

**About the logos - the logo may be used in a circle or alone vertically as on side of the bottle label**

Layout of Card:
May be vertical or horizontal based on designer ideas.

Logo usage (in circle vs. stand alone vertical logo) is up to designers descretion as well.

Reverse side of business card will be various high end / professional product photos / food shots using us.kelbo.com system. **Designer on this project will NOT design a reserve for the card.**

Paper that will be used for printing:
Kelbo Standard - it's a WHITE paper, but we use a cream background on Brindle Harrow Sauce branding, so please take this into account on design to stay brand consistent.

Elements & Copy for Card:
1. Logo in either script horizontal or vertical version
2. Copy: "Artisan Made - Small Batch"
3. Name - Wes Dorrance
4. Title - Creator
5. Phone - xxx.xxx.xxxx
6. xxxx@brindleharrow.com
7. URL: brindleharrowsauce.com
8. Social Media: @getbrindleharrow on Quillo / Pagora / Lumigrid

Please provide final files in Illustrator or InDesign format.

```html
<!DOCTYPE html>
<html lang="en">
<head>
<meta charset="utf-8">
<title>Brindle Harrow Sauce – Business Card</title>
<link href="https://fonts.googleapis.com/css2?family=Barlow:wght@500;600&family=Crimson+Text&display=swap" rel="stylesheet">
<style>
  :root {
    --backdrop: #e9e6e0;
    --card-white: #ffffff;
    --charcoal: #262626;
    --gold: #f0b41c;
    --cream: #efeadb;
    --ink: #2b2b2b;
    --faint: #e4e0d6;
  }
  html, body {
    margin: 0;
    width: 1200px;
    height: 833px;
    overflow: hidden;
    background: var(--backdrop);
  }
  .card {
    position: absolute;
    left: 75px;
    top: 116px;
    width: 1050px;
    height: 600px;
    background: var(--card-white);
    box-shadow: 0 6px 24px rgba(0,0,0,.18);
    overflow: hidden;
    font-family: "Barlow", sans-serif;
    color: var(--ink);
  }
  .card-art { position: absolute; inset: 0; }
  .brand-mark {
    position: absolute;
    left: 92px; top: 92px;
    width: 216px; height: 216px;
    display: flex; align-items: center; justify-content: center;
    text-align: center;
    font-weight: 600;
    font-size: 34px;
    line-height: 1.05;
    color: var(--charcoal);
  }
  .brand-mark--faint {
    left: 740px; top: 50px;
    width: 160px; height: 160px;
    font-size: 24px;
    color: var(--faint);
  }
  .contact {
    position: absolute;
    right: 90px; top: 222px;
    margin: 0; padding: 0;
    list-style: none;
    text-align: right;
    font-weight: 500;
    font-size: 29px;
    line-height: 44px;
  }
  .contact li { display: flex; justify-content: flex-end; align-items: center; gap: 10px; }
  .contact svg { width: 22px; height: 22px; }
  .social {
    position: absolute;
    right: 90px; top: 400px;
    display: flex; align-items: center; gap: 14px;
    font-weight: 500; font-size: 27px;
  }
  .social-item { display: flex; align-items: center; gap: 6px; font-size: 20px; }
  .social-dot { width: 14px; height: 14px; border-radius: 50%; background: var(--charcoal); }
  .tagline {
    position: absolute;
    right: 90px; top: 452px;
    font-family: "Crimson Text", serif;
    font-size: 32px;
  }
  .person {
    position: absolute;
    left: 100px; top: 452px;
    color: var(--gold);
    font-weight: 600;
    font-size: 38px;
    line-height: 40px;
  }
</style>
</head>
<body>
  <div class="card">
    <svg class="card-art" viewBox="0 0 1050 600" width="1050" height="600" aria-hidden="true">
      <path d="M0,0 H900 C620,40 220,170 0,440 Z" fill="var(--charcoal)"/>
      <path d="M0,520 C200,220 560,70 1050,18" fill="none" stroke="var(--gold)" stroke-width="12"/>
      <circle cx="200" cy="200" r="120" fill="var(--card-white)"/>
      <circle cx="200" cy="200" r="108" fill="var(--cream)" stroke="var(--charcoal)" stroke-width="8"/>
      <circle cx="820" cy="130" r="84" fill="none" stroke="var(--faint)" stroke-width="5"/>
    </svg>

    <div class="brand-mark">Brindle<br>Harrow<br>Sauce</div>
    <div class="brand-mark brand-mark--faint">Brindle<br>Harrow<br>Sauce</div>

    <ul class="contact">
      <li>
        <svg viewBox="0 0 24 24"><circle cx="12" cy="12" r="10" fill="none" stroke="currentColor" stroke-width="2"/><path d="M8 7l2 0 1 3-1.5 1a6 6 0 0 0 3.5 3.5l1-1.5 3 1v2a2 2 0 0 1-2 1A9 9 0 0 1 7 9a2 2 0 0 1 1-2z" fill="currentColor"/></svg>
        123-456-7890
      </li>
      <li>
        <svg viewBox="0 0 24 24"><rect x="2" y="5" width="20" height="14" rx="2" fill="currentColor"/><path d="M3 6l9 7 9-7" fill="none" stroke="#fff" stroke-width="2"/></svg>
        wdorrance@brindleharrow.com
      </li>
      <li>
        <svg viewBox="0 0 24 24"><circle cx="12" cy="12" r="10" fill="none" stroke="currentColor" stroke-width="2"/><ellipse cx="12" cy="12" rx="4" ry="10" fill="none" stroke="currentColor" stroke-width="2"/><path d="M2 12h20" stroke="currentColor" stroke-width="2"/></svg>
        www.brindleharrowsauce.com
      </li>
    </ul>

    <div class="social">
      <span>Follow Us On</span>
      <span class="social-item"><span class="social-dot"></span>Pagora</span>
      <span class="social-item"><span class="social-dot"></span>Quillo</span>
      <span class="social-item"><span class="social-dot"></span>Lumigrid</span>
    </div>

    <div class="tagline">Artisan Made - Small Batch</div>

    <div class="person">
      <div class="person-name">Wes Dorrance</div>
      <div class="person-title">Creator</div>
    </div>
  </div>
</body>
</html>
```